Family business needs stationery redesign with new logo

Family owned company, established in 1987 wanting a brand 'refresh'. We are an electrical, refrigeration and construction company based in the Barkly Region Northern Territory, Australia. We have a new logo we would like to use which is uploaded along with our current letterhead and email signature. We are also dropping the word 'contractors' so please do not include this on any designs. Please note also, the 'orange' color used in our logo and designs should be Northern Territory red ochre which is as follows:

RGB (Hex): #C75B12
PantoneĀ® 159 C
CMYK: 1 / 74 / 100 / 7

We are needing our stationery redesigned using our new logo. Please include letterheads, business cards, envelopes, and email signatures.

We currently use our business letterheads for quotations, invoices, letters, HR matters, and internal memos.

We also need a separate simplified letterhead for internal paperwork such as employee leave forms, meeting agendas, and meeting minutes etc.

Reason: Needing more submissions of full package designs. We are wanting all our stationery, including business cards, letterheads, email signatures, envelopes, etc to be cohesive. We also require ALL the information, as supplied on our template letterhead, to be included on the new letterhead designs. including electrical license no.etc Thank you, R&W

Reason: needing more time as work has got in the way of looking over designs. A lot of designs not meeting the brief/criteria.

Industry/Entity Type

Business

Colors
0355a3
f37122

Requirements
Must have
• The 'orange' color used in the designs should be Northern Territory red ochre which is as follows:
• RGB (Hex): #C75B12
• PantoneĀ® 159 C
• CMYK: 1 / 74 / 100 / 7
• ***MUST INCLUDE ALL INFORMATION THAT IS ON OUR CURRENT LETTERHEAD***
Should not have
• Please do not include the word 'contractors'

```html
<!DOCTYPE html>
<html lang="en">
<head>
<meta charset="utf-8">
<title>R&amp;W Stationery</title>
<link href="https://fonts.googleapis.com/css2?family=Tinos:wght@400;700&family=Arimo:wght@400;700&family=Exo+2:wght@400&display=swap" rel="stylesheet">
<style>
:root{
  --navy:#1b3270;
  --ochre:#c75b12;
  --paper:#ffffff;
  --ground:#ececec;
  --ink:#333333;
}
*{box-sizing:border-box;margin:0;padding:0}
html,body{width:1200px;height:938px;overflow:hidden;background:var(--ground)}
.canvas{position:relative;width:1200px;height:938px}
.sheet{position:absolute;background:var(--paper);overflow:hidden}
.band{position:absolute;left:0;bottom:0;width:100%}
.brand{position:absolute;display:flex;align-items:center;gap:8px}
.brand-name{font-family:"Tinos",serif;font-weight:700;color:var(--navy);line-height:1}
.brand-tag{font-family:"Tinos",serif;color:var(--navy);line-height:1.2}
.web{font-family:"Exo 2",sans-serif;color:#fff;letter-spacing:.28em;position:absolute}

/* letterhead */
.letterhead{left:184px;top:68px;width:386px;height:544px}
.letterhead .brand{left:18px;top:26px}
.letterhead .brand-name{font-size:30px}
.letterhead .brand-tag{font-size:8px}
.letter{position:absolute;left:38px;top:138px;width:296px;font-family:"Arimo",sans-serif;color:var(--ink);font-size:5.4px;line-height:8.4px}
.letter p{margin-bottom:8px}
.letter .gap{margin-bottom:24px}
.signature{width:40px;height:22px;background:linear-gradient(90deg,#e6e6e6,#d4d4d4);margin:6px 0 8px}
.letter strong{font-weight:700}
.contact{position:absolute;right:13px;bottom:6px;text-align:right;font-family:"Exo 2",sans-serif;color:#fff;font-size:6px;line-height:11.5px}
.contact .addr{font-size:6.4px;line-height:8.5px;margin-bottom:5px}
.contact .small{font-size:5px;line-height:8px}
.icon{display:inline-block;width:5px;height:5px;vertical-align:middle;margin-left:3px}

/* folder */
.folder{left:637px;top:42px;width:457px;height:574px}
.folder .brand{left:0;right:0;top:235px;flex-direction:column;gap:10px}
.folder .brand-name{font-size:48px}
.folder .brand-tag{font-size:16px;text-align:center;line-height:18.5px}
.folder .web{left:0;right:0;bottom:10px;text-align:center;font-size:10.5px}

/* business cards */
.card{left:46px;width:176px;height:99px;border-radius:7px}
.card-front{top:660px}
.card-back{top:786px}
.card-front .brand{left:10px;top:9px;gap:6px}
.card-front .brand-name{font-size:15px}
.card-front .brand-tag{font-size:4.3px}
.holder{position:absolute;left:12px;top:38px;font-family:"Arimo",sans-serif;color:var(--navy)}
.holder .name{font-size:5.2px;letter-spacing:.06em}
.holder .role{font-size:3.6px;font-weight:700;color:#222}
.card-lines{position:absolute;right:8px;top:58px;text-align:right;font-family:"Arimo",sans-serif;font-size:3.4px;line-height:6.4px;color:#fff}
.card-addr{position:absolute;left:11px;bottom:7px;font-family:"Exo 2",sans-serif;color:#fff;font-size:4.4px;line-height:6px}
.card-back .brand{left:42px;top:36px;gap:6px}
.card-back .brand-name{font-size:18px}
.card-back .brand-tag{font-size:4.8px}

/* envelope front */
.envelope{left:266px;top:674px;width:431px;height:208px}
.envelope .brand{left:16px;top:23px;gap:10px}
.envelope .brand-name{font-size:28px}
.envelope .brand-tag{font-size:8px}
.envelope .web{right:14px;bottom:8px;font-size:9px}

/* envelope back */
.envelope-back{left:737px;top:672px;width:432px;height:208px}
.flap{position:absolute;left:0;top:0;width:100%;height:72px;background:var(--ochre);border-radius:0 0 42px 42px}
.flap .web{left:0;right:0;top:28px;text-align:center;font-size:10.5px}
</style>
</head>
<body>
<div class="canvas">

  <section class="sheet letterhead">
    <div class="brand">
      <span class="brand-name">R&amp;W</span>
      <span class="brand-tag">Electrical<br>Refrigeration<br>Building Services</span>
    </div>
    <div class="letter">
      <p>July 2, 2012</p>
      <p><strong>Dear CH,</strong><br>ABC Building, def St., Country Name</p>
      <p class="gap">This letter confirms the scope of work discussed at our recent site visit. Our team will complete the electrical upgrade, replace the cold room refrigeration unit and repair the storage shed roof. All works will meet current standards and will be carried out by licensed tradespeople. A full quotation is attached for your review, and we are happy to answer any questions before the work is scheduled to begin.</p>
      <p class="gap">Please note that site access will be needed from seven each morning, and power may be off for short periods during the changeover.</p>
      <p>Payment terms are thirty days from the date of invoice. Should you wish to proceed, please sign and return the attached acceptance form so we can book materials and confirm a start date with you. Thank you for choosing our family business; we look forward to working with you again on this project.</p>
      <p>Best Regards,</p>
      <div class="signature" role="img" aria-label="Handwritten signature"></div>
      <p><strong>Daniel Ross</strong><br>Director</p>
      <p>ABC Building, def St., Country Name</p>
    </div>
    <svg class="band" height="124" viewBox="0 0 400 120" preserveAspectRatio="none" aria-hidden="true">
      <polygon points="0,40 400,0 400,10 0,50" fill="var(--ochre)"/>
      <polygon points="0,58 400,18 400,120 0,120" fill="var(--navy)"/>
    </svg>
    <div class="contact">
      <div class="addr">14 Ochre Street<br>Barkly NT</div>
      <div>08 8962 4410<svg class="icon" viewBox="0 0 10 10"><path d="M2 1l2 2-1 1.5c.8 1.5 1.5 2.2 3 3L7.5 6l2 2-1.5 1.5C4.5 9 1 5.5.5 2.5Z" fill="#fff"/></svg></div>
      <div>0417 305 228<svg class="icon" viewBox="0 0 10 10"><rect x="2.5" y=".5" width="5" height="9" rx="1" fill="none" stroke="#fff"/></svg></div>
      <div>08 8962 4411<svg class="icon" viewBox="0 0 10 10"><rect x="1" y="4" width="8" height="5" fill="#fff"/><rect x="3" y="1" width="4" height="3" fill="#fff"/></svg></div>
      <div class="small">office@rwbarkly.example<svg class="icon" viewBox="0 0 10 10"><rect x=".5" y="2" width="9" height="6" fill="#fff"/></svg></div>
      <div class="small">www.rwbarkly.example<svg class="icon" viewBox="0 0 10 10"><circle cx="5" cy="5" r="4.2" fill="none" stroke="#fff"/><path d="M1 5h8M5 1v8" stroke="#fff"/></svg></div>
    </div>
  </section>

  <section class="sheet folder">
    <div class="brand">
      <span class="brand-name">R&amp;W</span>
      <span class="brand-tag">Electrical<br>Refrigeration<br>Building Services</span>
    </div>
    <svg class="band" height="140" viewBox="0 0 400 120" preserveAspectRatio="none" aria-hidden="true">
      <polygon points="0,40 400,0 400,10 0,50" fill="var(--ochre)"/>
      <polygon points="0,58 400,18 400,120 0,120" fill="var(--navy)"/>
    </svg>
    <div class="web">www.rwbarkly.example</div>
  </section>

  <section class="sheet card card-front">
    <div class="brand">
      <span class="brand-name">R&amp;W</span>
      <span class="brand-tag">Electrical<br>Refrigeration<br>Building Services</span>
    </div>
    <svg class="band" height="56" viewBox="0 0 400 120" preserveAspectRatio="none" aria-hidden="true">
      <polygon points="0,40 400,0 400,10 0,50" fill="var(--ochre)"/>
      <polygon points="0,58 400,18 400,120 0,120" fill="var(--navy)"/>
    </svg>
    <div class="holder"><div class="name">PETER LAWSON</div><div class="role">Managing Director</div></div>
    <div class="card-lines">08 8962 4410<br>0417 305 228<br>08 8962 4411<br>office@rwbarkly.example<br>www.rwbarkly.example</div>
    <div class="card-addr">14 Ochre Street<br>Barkly NT</div>
  </section>

  <section class="sheet card card-back">
    <div class="brand">
      <span class="brand-name">R&amp;W</span>
      <span class="brand-tag">Electrical<br>Refrigeration<br>Building Services</span>
    </div>
  </section>

  <section class="sheet envelope">
    <div class="brand">
      <span class="brand-name">R&amp;W</span>
      <span class="brand-tag">Electrical<br>Refrigeration<br>Building Services</span>
    </div>
    <svg class="band" height="88" viewBox="0 0 400 120" preserveAspectRatio="none" aria-hidden="true">
      <polygon points="0,40 400,0 400,10 0,50" fill="var(--ochre)"/>
      <polygon points="0,58 400,18 400,120 0,120" fill="var(--navy)"/>
    </svg>
    <div class="web">www.rwbarkly.example</div>
  </section>

  <section class="sheet envelope-back">
    <div class="flap"><div class="web">www.rwbarkly.example</div></div>
  </section>

</div>
</body>
</html>
```